Business Card for a Jewellery Brand

Business card for an upscale jewellery brand. Attached is the brand logo and icon and color board. I am looking for two card versions: one for the founder and one is generic. The card should be elegant and convey upscale and premium feel. I am open to both square and rectangle card shapes.

Industry/Entity Type

Jewelry

Contact Information for Business Card

Two cards: (1) Sunela Parvaniya (Founder) (2) General
(1) Sunela Parvaniya card should have Name: Sunela Parvaniya, Title: Founder Email id: sunela@quiremo.com.au. Phone no: +61452913307
(2) Generic card should have Email id: info@quiremo.com.au. Phone no: +61436207518

Requirements
Must have
• Workmark
• ICON
• Phone no
• Email ID
• ABN: 58219740312 (Note: ABN is Business number in Australia)
• Website: www.quiremo.com.au
• Instagram: quiremo_jewellery
• Facebook: @quiremojewellery
Nice to have
• Tagline

```html
<!DOCTYPE html>
<html lang="en">
<head>
<meta charset="utf-8">
<title>Quiremo – Founder Business Card</title>
<link rel="stylesheet" href="https://fonts.googleapis.com/css2?family=Barlow:wght@300;400&family=Barlow+Semi+Condensed:wght@600&display=swap">
<style>
  :root {
    --backdrop: #e4e1dd;
    --card: #f2f0ee;
    --card-edge: #dcd8d4;
    --brand-red: #b83a45;
    --ink: #3d3a3a;
    --abn: #d07a80;
  }
  html, body {
    margin: 0;
    width: 1200px;
    height: 969px;
    overflow: hidden;
    background: var(--backdrop);
  }
  .canvas {
    position: relative;
    width: 1200px;
    height: 969px;
  }
  .card {
    position: absolute;
    left: 120px;
    top: 211px;
    width: 960px;
    height: 546px;
    border-radius: 24px;
    background: var(--card);
    border: 1px solid var(--card-edge);
    box-shadow: 0 18px 40px rgba(0,0,0,0.10);
    overflow: hidden;
  }
  .wordmark {
    position: absolute;
    left: 64px;
    top: 72px;
    margin: 0;
    font-family: "Barlow", sans-serif;
    font-weight: 300;
    font-size: 54px;
    letter-spacing: 14px;
    line-height: 1;
    color: var(--brand-red);
  }
  .person {
    position: absolute;
    left: 66px;
    top: 184px;
  }
  .person-name {
    margin: 0;
    font-family: "Barlow Semi Condensed", sans-serif;
    font-weight: 600;
    font-size: 30px;
    letter-spacing: 0.5px;
    text-transform: uppercase;
    color: var(--brand-red);
    line-height: 1.1;
  }
  .person-title {
    margin: 4px 0 0;
    font-family: "Barlow", sans-serif;
    font-weight: 400;
    font-size: 22px;
    color: var(--ink);
  }
  .contact-list {
    position: absolute;
    left: 66px;
    top: 280px;
    margin: 0;
    padding: 0;
    list-style: none;
    font-family: "Barlow", sans-serif;
    font-weight: 400;
    font-size: 22px;
    color: var(--ink);
  }
  .contact-list li {
    display: flex;
    align-items: center;
    height: 29px;
  }
  .contact-icon {
    width: 18px;
    height: 18px;
    margin-right: 12px;
    flex: none;
  }
  .abn {
    position: absolute;
    left: 66px;
    top: 454px;
    margin: 0;
    font-family: "Barlow", sans-serif;
    font-weight: 400;
    font-size: 22px;
    color: var(--abn);
  }
  .brand-emblem {
    position: absolute;
    left: 470px;
    top: 40px;
    width: 460px;
    height: 466px;
    display: flex;
    flex-direction: column;
    align-items: center;
    justify-content: center;
  }
  .emblem-circle {
    width: 290px;
    height: 290px;
    border-radius: 50%;
    border: 10px solid var(--brand-red);
    box-sizing: border-box;
  }
  .emblem-name {
    margin: 34px 0 0;
    font-family: "Barlow", sans-serif;
    font-weight: 300;
    font-size: 46px;
    letter-spacing: 12px;
    color: var(--brand-red);
  }
</style>
</head>
<body>
<main class="canvas">
  <section class="card" aria-label="Quiremo founder business card">
    <h1 class="wordmark">QUIREMO</h1>

    <div class="person">
      <p class="person-name">Sunela Parvaniya</p>
      <p class="person-title">Founder</p>
    </div>

    <ul class="contact-list">
      <li>
        <svg class="contact-icon" viewBox="0 0 18 18" aria-hidden="true">
          <rect x="4" y="1" width="10" height="16" rx="2" fill="none" stroke="var(--brand-red)" stroke-width="2"/>
          <circle cx="9" cy="14" r="1" fill="var(--brand-red)"/>
        </svg>
        +61452913307
      </li>
      <li>
        <svg class="contact-icon" viewBox="0 0 18 18" aria-hidden="true">
          <rect x="1" y="4" width="16" height="11" fill="var(--brand-red)"/>
          <path d="M1 4 L9 10 L17 4" fill="none" stroke="var(--card)" stroke-width="1.5"/>
        </svg>
        sunela@quiremo.com.au
      </li>
      <li>
        <svg class="contact-icon" viewBox="0 0 18 18" aria-hidden="true">
          <circle cx="9" cy="9" r="7.5" fill="none" stroke="var(--brand-red)" stroke-width="2"/>
          <path d="M1.5 9 H16.5 M9 1.5 C5 5 5 13 9 16.5 C13 13 13 5 9 1.5" fill="none" stroke="var(--brand-red)" stroke-width="1.3"/>
        </svg>
        www.quiremo.com.au
      </li>
      <li>
        <svg class="contact-icon" viewBox="0 0 18 18" aria-hidden="true">
          <rect x="2" y="2" width="14" height="14" rx="2" fill="var(--brand-red)"/>
        </svg>
        quiremo_jewellery
      </li>
      <li>
        <svg class="contact-icon" viewBox="0 0 18 18" aria-hidden="true">
          <rect x="2" y="2" width="14" height="14" rx="2" fill="var(--brand-red)"/>
        </svg>
        @quiremojewellery
      </li>
    </ul>

    <p class="abn">ABN: 58219740312</p>

    <div class="brand-emblem">
      <div class="emblem-circle"></div>
      <p class="emblem-name">QUIREMO</p>
    </div>
  </section>
</main>
</body>
</html>
```